Road Construction Company needs business cards

We would like a new business card designed for our business.

We're a road construction company based in Qld, Australia.

Can the business card please have the following information on it.

Name: Warren Halbeck
Position: General Manager
Phone: 0472 915 348
Email: Warren.halbeck@tovrin.com.au
Address: 87 Marrow Ave, Pendlebay, QLD, 4023
Website: www.tovrin.com.au

Visually we'd like the card to be professional and simple.

Attached is our logo.

Our website is www.tovrin.com.au

Target Market(s)

Men aged 25-60

Contact Information for Business Card

As listed in project description

Font styles to use
Serif

Requirements
Must have
• Large logo on back of card

```html
<!DOCTYPE html>
<html lang="en">
<head>
<meta charset="utf-8">
<title>Tovrin Business Card</title>
<link href="https://fonts.googleapis.com/css2?family=Exo+2:wght@400;800&display=swap" rel="stylesheet">
<style>
  :root {
    --brand-blue: #0552a8;
    --accent-blue: #2fa3d8;
    --paper: #ffffff;
    --backdrop: #1f1f1f;
    --backdrop-edge: #0e0e0e;
  }
  * { margin: 0; padding: 0; box-sizing: border-box; }
  html, body { width: 1200px; height: 1015px; overflow: hidden; }
  body {
    background: radial-gradient(ellipse at center, var(--backdrop) 0%, var(--backdrop-edge) 100%);
    font-family: "Exo 2", sans-serif;
    position: relative;
  }
  .card {
    position: absolute;
    left: 220px;
    width: 760px;
    height: 434px;
    overflow: hidden;
    background: var(--brand-blue);
    box-shadow: 0 10px 30px rgba(0,0,0,.55);
  }
  .card--back { top: 48px; }
  .card--front { top: 532px; }

  .back-wordmark {
    position: absolute;
    inset: 0;
    display: flex;
    align-items: center;
    justify-content: center;
    color: var(--paper);
    font-weight: 800;
    font-size: 78px;
    letter-spacing: 6px;
  }

  .front-shape { position: absolute; inset: 0; }
  .front-wordmark {
    position: absolute;
    left: 420px;
    top: 176px;
    width: 300px;
    text-align: center;
    color: var(--brand-blue);
    font-weight: 800;
    font-size: 52px;
    letter-spacing: 4px;
  }

  .contact { position: absolute; color: var(--paper); }
  .contact__name {
    left: 52px; top: 104px;
    font-weight: 800; font-size: 27px; letter-spacing: 1px; text-transform: uppercase;
  }
  .contact__role { left: 54px; top: 138px; font-size: 18px; }
  .contact__address { left: 110px; top: 210px; font-size: 17px; line-height: 1.35; }
  .contact__lines {
    left: 110px; top: 316px; list-style: none; font-size: 17px; line-height: 1.45;
  }
  .contact__lines li { display: flex; align-items: center; gap: 10px; }
  .contact__lines svg { width: 15px; height: 15px; flex: none; }
</style>
</head>
<body>

<section class="card card--back" aria-label="Card back">
  <div class="back-wordmark">TOVRIN</div>
</section>

<section class="card card--front" aria-label="Card front">
  <svg class="front-shape" viewBox="0 0 760 434" aria-hidden="true">
    <circle cx="575" cy="170" r="262" fill="var(--accent-blue)"/>
    <circle cx="592" cy="166" r="258" fill="var(--paper)"/>
  </svg>
  <div class="front-wordmark">TOVRIN</div>

  <div class="contact contact__name">Warren Halbeck</div>
  <div class="contact contact__role">General Manager</div>
  <div class="contact contact__address">87 Marrow Ave<br>Pendlebay, QLD, 4023</div>
  <ul class="contact contact__lines">
    <li>
      <svg viewBox="0 0 16 16"><path fill="var(--paper)" d="M3.6 1.5l2.3 2.6-1.2 1.8c.9 2 2.5 3.6 4.5 4.5l1.8-1.2 2.6 2.3-1.4 2.5C6.7 13.8 2.2 9.3 1.1 2.9z"/></svg>
      0472 915 348
    </li>
    <li>
      <svg viewBox="0 0 16 16"><rect x="1" y="3" width="14" height="10" fill="var(--paper)"/><path d="M1 3l7 6 7-6" fill="none" stroke="var(--brand-blue)" stroke-width="1.2"/></svg>
      Warren.halbeck@tovrin.com.au
    </li>
    <li>
      <svg viewBox="0 0 16 16"><circle cx="8" cy="8" r="6.5" fill="none" stroke="var(--paper)" stroke-width="1.4"/><ellipse cx="8" cy="8" rx="2.8" ry="6.5" fill="none" stroke="var(--paper)" stroke-width="1.1"/><path d="M1.5 8h13M2.5 5h11M2.5 11h11" stroke="var(--paper)" stroke-width="1"/></svg>
      www.tovrin.com.au
    </li>
  </ul>
</section>

</body>
</html>
```